Custom billboard campaign - Construction

We are starting a new billboard campaign and we need a design for our print billboards. We are a post-frame building company that builds custom buildings. We build homes, agricultural buildings, commercial buildings, and suburban/ hobby shops.
We would like to have our phone number (309)582-1936 as well as our website www.kestrovanframing.com
Text- Your post-frame experts!
Agriculture- Commercial - Homes - Suburban
Colors:
Black, chrome, white
We want our final design to be professional as well as luxurious/ high-end. I have attached our logo as well as building photos.
Construction - building

```html
<!DOCTYPE html>
<html lang="en">
<head>
<meta charset="utf-8">
<title>Kestrovan Framing Billboard</title>
<link href="https://fonts.googleapis.com/css2?family=Montserrat:wght@400;500;800&display=swap" rel="stylesheet">
<style>
  :root {
    --ink: #000000;
    --page: #ffffff;
    --white: #ffffff;
    --chrome-light: #f2f2f2;
    --chrome-mid: #a9abae;
    --chrome-dark: #6f7275;
    --plate-text: #1a1a1a;
  }
  * { margin: 0; padding: 0; box-sizing: border-box; }
  html, body { width: 1006px; height: 1200px; overflow: hidden; background: var(--page); }
  .billboard {
    position: absolute; left: 20px; top: 358px;
    width: 966px; height: 483px;
    background: var(--ink);
    overflow: hidden;
    font-family: "Montserrat", sans-serif;
    color: var(--white);
  }
  .billboard-art { position: absolute; inset: 0; width: 966px; height: 483px; }
  .chrome {
    background: linear-gradient(180deg, var(--chrome-light) 0%, var(--chrome-mid) 55%, var(--chrome-light) 75%, var(--chrome-dark) 100%);
    -webkit-background-clip: text; background-clip: text; color: transparent;
  }
  .headline {
    position: absolute; left: 43px; top: 30px;
    font-weight: 800; font-size: 60px; line-height: 62px; letter-spacing: -1.5px;
  }
  .headline-rule { position: absolute; left: 45px; top: 238px; width: 57px; height: 4px; background: var(--white); }
  .services { position: absolute; top: 268px; font-size: 28px; line-height: 38px; font-weight: 400; }
  .services li { list-style: none; display: flex; align-items: center; gap: 8px; }
  .services-left { left: 45px; }
  .services-right { left: 298px; }
  .services-divider { position: absolute; left: 281px; top: 274px; width: 2px; height: 60px; background: var(--white); }
  .tick { width: 28px; height: 28px; flex: none; }
  .call-label {
    position: absolute; left: 45px; top: 385px;
    font-size: 23px; letter-spacing: 1px; font-weight: 400;
    display: flex; align-items: center; gap: 10px;
  }
  .call-label::after { content: ""; width: 78px; height: 2px; background: var(--white); }
  .phone-icon { position: absolute; left: 45px; top: 421px; width: 46px; height: 46px; }
  .phone-number {
    position: absolute; left: 106px; top: 414px;
    font-weight: 800; font-size: 46px; line-height: 58px; letter-spacing: -0.5px;
  }
  .web-plate {
    position: absolute; left: 491px; top: 417px; width: 437px; height: 50px;
    background: linear-gradient(90deg, var(--chrome-mid) 0%, var(--chrome-light) 45%, #c9cacc 70%, var(--chrome-mid) 100%);
    color: var(--plate-text);
    font-size: 27px; font-weight: 500;
    display: flex; align-items: center; justify-content: center;
  }
  .brand-mark {
    position: absolute; left: 820px; top: 28px; width: 140px;
    text-align: center; color: var(--ink);
    font-weight: 800; font-size: 15px; line-height: 17px; letter-spacing: 2px;
  }
</style>
</head>
<body>
<main class="billboard">
  <svg class="billboard-art" viewBox="0 0 966 483">
    <defs>
      <linearGradient id="photoTones" x1="0" y1="0" x2="0" y2="1">
        <stop offset="0" stop-color="#b9c4cf"/>
        <stop offset="0.25" stop-color="#8e3a40"/>
        <stop offset="0.55" stop-color="#a3242d"/>
        <stop offset="0.72" stop-color="#4f5a3e"/>
        <stop offset="1" stop-color="#a79d8c"/>
      </linearGradient>
    </defs>
    <path class="crescent" fill="#ffffff" d="M528,92 C442,190 455,330 598,386 C700,420 800,402 842,380 C720,398 562,370 502,280 C462,212 480,140 528,92 Z"/>
    <path class="building-photo" role="img" aria-label="Photo of a red post-frame building with grey doors, covered porch and landscaped gravel garden" fill="url(#photoTones)" d="M552,0 L966,0 L966,290 C870,370 660,392 560,332 C470,272 452,150 520,60 C535,35 545,15 552,0 Z"/>
  </svg>

  <div class="brand-mark">KESTROVAN<br>FRAMING, INC.</div>

  <h1 class="headline chrome">Your<br>Post-frame<br>Experts!</h1>
  <div class="headline-rule"></div>

  <ul class="services services-left">
    <li><svg class="tick" viewBox="0 0 28 28"><circle cx="13" cy="15" r="10" fill="none" stroke="#fff" stroke-width="2.2"/><path d="M8 15 l4 4 l12 -13" fill="none" stroke="#fff" stroke-width="2.6" stroke-linecap="round" stroke-linejoin="round"/></svg>Agriculture</li>
    <li><svg class="tick" viewBox="0 0 28 28"><circle cx="13" cy="15" r="10" fill="none" stroke="#fff" stroke-width="2.2"/><path d="M8 15 l4 4 l12 -13" fill="none" stroke="#fff" stroke-width="2.6" stroke-linecap="round" stroke-linejoin="round"/></svg>Commercial</li>
  </ul>
  <div class="services-divider"></div>
  <ul class="services services-right">
    <li><svg class="tick" viewBox="0 0 28 28"><circle cx="13" cy="15" r="10" fill="none" stroke="#fff" stroke-width="2.2"/><path d="M8 15 l4 4 l12 -13" fill="none" stroke="#fff" stroke-width="2.6" stroke-linecap="round" stroke-linejoin="round"/></svg>Homes</li>
    <li><svg class="tick" viewBox="0 0 28 28"><circle cx="13" cy="15" r="10" fill="none" stroke="#fff" stroke-width="2.2"/><path d="M8 15 l4 4 l12 -13" fill="none" stroke="#fff" stroke-width="2.6" stroke-linecap="round" stroke-linejoin="round"/></svg>Suburban</li>
  </ul>

  <p class="call-label">CALL US TODAY!</p>
  <svg class="phone-icon" viewBox="0 0 46 46">
    <circle cx="23" cy="23" r="21" fill="none" stroke="#fff" stroke-width="2.5"/>
    <path d="M15 13 l4 -1 l3 6 l-3 2 c1 3 3 5 6 6 l2 -3 l6 3 l-1 4 c-9 1 -18 -8 -17 -17 Z" fill="#fff"/>
    <path d="M25 13 a8 8 0 0 1 8 8 M25 9 a12 12 0 0 1 12 12" fill="none" stroke="#fff" stroke-width="2"/>
  </svg>
  <p class="phone-number chrome">(309)582-1936</p>
  <div class="web-plate">www.kestrovanframing.com</div>
</main>
</body>
</html>
```